Meridel Super Yacht Party Ibiza

PSD ONLY PROJECT
We need our first Website for brand new Super Yacht Party - Meridel.
We have some ideas on brand concepts and colours attached but are looking for something unique with a great layout and visually appealing.
We are looking for interesting ways to display and edit pictures - maybe with blur or watermark square over lays etc so the image is distorted somewhat.
Company Logo is attached and company font is Calvant Serif
Meridel the brand is aimed at the luxury market, this is for people who will spend 3 hours of their holiday partying on a super yacht, drinking champagne, easting Sushi, chilling on our VIP Beds and watching the sunset.
We are not looking for anything Nautical themed - so please no life buoys, stripes, portholes or wheels.
The website needs to ooze class and sophistication while also appealing to party hard music loving lubbers from Ibiza - this will be the tricky part to get right!
It needs to be visual and eye catching - we don't have any pre conceived ideas nessacarily so consider this a blank canvas.
I have added photos this project but if you have any others then please feel free to add them - don´t worry about watermarks we can remove them at a later stage.
Pages:
Homepage
The Yacht
VIP
Tickets [no page design necessary for tickets]
Contact
FAQ
Recruitment
HOMEPAGE:
The homepage needs to tell people about the event and give them instant affinity with the brand and what the party offers.
There needs to be a subscribe function for the newsletter.
There needs to be Social Feeds.
THE YACHT:
This needs to sell people to go on the Yacht they are going on see below for all points, needs to look luxurious and glamorous
VIP:
This needs to display the VIP options and encourage people to click to make an enquiry [handled through email]
CONTACT:
List of people to contact and company information - use any information for design stage
FAQ:
A list of common questions and answers displayed in a unique way copy provided at a later date.
RECRUITMENT:
Space for some copy about different jobs and click to apply handled through email
HOMEPAGE
The Ibiza boat party market is about to take a giant leap forward as 2015 sees the launch of brand new Super Yacht Event – Meridel.
Created by titans of the Ibiza boat and club scene with over 10 years experience the Meridel Super Yacht Parties will define a dawn of a new age for Ibiza Boat Parties where they are no longer confined to the top deck of a sight seeing catamaran.
Sailing exclusively from San Antonio in 2015, which is the only place to be seen capturing the islands iconic sunset. The San Antonio sunset has served as a backdrop for every major music revolution on the island and the Meridel Super Yacht Experience pulls no punches.
NOT ALL BOAT PARTIES ARE CREATED EQUAL
SUPER YACHT EXPERIENCE
ICONIC IBIZA SUNSET
4 FLOORS OF MUSIC
DEEP AND TECH HOUSE
KRAL SOUNDSYSTEM
VIP ROOMS AND BEDS AVAILABLE
ON BOARD LOCAL FASHION & MERCH SHOP
BOTTLE SERVICE TO TABLES
CHAMPAGNE SPRAY
€100 VODKA BOTTLE
WILDEST PARTY
HOTTEST GIRLS AND GUYS
ON BOARD HOT TUB
ISLANDS BEST ARIEL PRODUCTION AT SEA
VIP PAGE
Choose from
The ultimate in VIP on our luxury beds and in our themed rooms with full table service where everything is catered for.
Speak to our concierge team to make your reservation now.
TOP DECK BEDS
HOT TUB
MID DECK TABLES
UNDERWATER THEMED ROOMS
SUPER YACHT STATS
The Super Yacht has some impressive stats:
• The ultimate in VIP with full table service!
• Top Deck Beds with complimentary towels and Hot Tub!
• Underwater Rooms – secluded and themed with a private bed and window!
• Mid and Lower Deck Tables – in the heart of the action!
• 6 Luxury Toilets – no more long queues or nasty niffs!
• 4 Impressive Floors – There is space for everyone whether chilling or raving!
• 4 Premium Bars – don´t delay the party queuing for a drink!
• 1 Restaurant – Sushi, Finger Food and More from our on board Chefs.
• 1 Shop – Taking a break from the party? Local island trinkets with our own twist!
• 1 Brand New KRAL sound system – crystal clear sound to every floor with the finest Deep and Tech beats from our international resident team.
• The finest in production but not just limited to the boat as we fly in an International Water Stunt artist team to delight guests.
See following website for inspiration:
http://www.tidelumeparty.com
http://www.velmorastays.com
http://www.porvaleclubs.com/destinations/beach-clubs/marbella/
http://www.zentrovia.es
Any questions please let me know!!

```html
<!DOCTYPE html>
<html lang="en">
<head>
<meta charset="utf-8">
<title>Meridel — Super Yacht Party Ibiza</title>
<link href="https://fonts.googleapis.com/css2?family=Montserrat:wght@300;400;700&family=Roboto+Condensed:wght@300;400;700&family=Roboto:wght@300;400&display=swap" rel="stylesheet">
<style>
:root{
  --bg-dark:#1e170f;
  --bg-mid:#3a2e1f;
  --gold:#c9a53e;
  --gold-light:#e6c660;
  --gold-deep:#8a6f25;
  --panel:#1b1610;
  --text:#f3ede0;
  --muted:#a8987a;
}
*{margin:0;padding:0;box-sizing:border-box}
html,body{width:1200px;height:1200px;overflow:hidden;background:var(--bg-dark)}
body{position:relative;font-family:"Roboto",sans-serif;color:var(--text)}
.backdrop{position:absolute;inset:0;background:radial-gradient(ellipse at 50% 30%,#5a4830 0%,#3a2e1f 45%,#1e170f 100%)}
.hero-photo{position:absolute;left:250px;top:90px;width:700px;height:200px;background:radial-gradient(ellipse at 45% 40%,#8f8378 0%,#6a5a48 45%,rgba(58,46,31,0) 100%)}

.logo{position:absolute;left:248px;top:14px;display:flex;align-items:center;gap:8px}
.logo-mark{width:52px;height:52px;border-radius:50%;border:3px solid var(--gold)}
.logo-name{font-family:"Montserrat",sans-serif;font-weight:400;font-size:17px;line-height:19px;letter-spacing:1px;color:var(--text)}
.logo-sub{font-family:"Montserrat",sans-serif;font-weight:400;font-size:7px;letter-spacing:.5px;color:var(--text)}

.nav{position:absolute;right:250px;top:12px;height:20px;display:flex;align-items:center;gap:14px;font-family:"Roboto Condensed",sans-serif;font-size:12px;line-height:20px;color:var(--text)}
.nav-search{display:block;width:18px;height:18px}
.reserve-title{position:absolute;right:250px;top:36px;font-family:"Montserrat",sans-serif;font-size:11px;line-height:13px;letter-spacing:.5px;white-space:nowrap}
.reserve-title b{font-weight:700}
.reserve-line{position:absolute;right:250px;top:50px;font-family:"Roboto Condensed",sans-serif;font-size:7.5px;line-height:9px;white-space:nowrap}
.reserve-line span{color:var(--gold)}
.social{position:absolute;right:250px;top:69px;display:flex;align-items:center;gap:4px;font-family:"Montserrat",sans-serif;font-size:11px;line-height:17px}
.social b{font-weight:700}
.social-label{margin-right:2px}
.social-dot{width:17px;height:17px;border-radius:50%;background:var(--gold)}

.welcome{position:absolute;left:258px;top:202px}
.welcome-small{display:inline-block;background:#120e09;padding:3px 8px;font-family:"Montserrat",sans-serif;font-weight:400;font-size:19px;line-height:22px;color:var(--text)}
.welcome-big{display:block;width:232px;margin-top:2px;background:#120e09;padding:0 8px;font-family:"Montserrat",sans-serif;font-weight:700;font-size:44px;line-height:47px;color:var(--text)}

.panel{position:absolute;left:250px;top:286px;width:700px;height:620px;background:rgba(27,22,16,.88);border:3px dashed var(--gold-deep)}
.intro{position:absolute;left:316px;top:306px;width:574px;text-align:center;font-weight:300;font-size:13px;line-height:17px}
.intro p+p{margin-top:17px}

.photo-circle{position:absolute;width:144px;height:144px;border-radius:50%;top:454px}
.claim{position:absolute;left:514px;top:438px;width:172px;height:172px;border-radius:50%;background:radial-gradient(circle,#a88b3a,#7d6526);display:flex;align-items:center;justify-content:center;text-align:center;font-family:"Roboto Condensed",sans-serif;font-weight:700;font-size:18px;line-height:16.5px}

.features{position:absolute;left:250px;top:632px;width:700px;display:grid;grid-template-columns:337px 27px 1fr;font-family:"Roboto Condensed",sans-serif;font-weight:300;font-size:16px;line-height:21px}
.features ul{list-style:none}
.features .left{text-align:right}
.features .dots{text-align:center;color:var(--gold)}

.events-title{position:absolute;left:0;width:1200px;top:828px;text-align:center;font-family:"Montserrat",sans-serif;font-weight:300;font-size:22px;line-height:26px;letter-spacing:.5px;color:var(--gold)}
.events-title b{font-weight:700;color:var(--gold-light)}
.events-yacht{position:absolute;left:348px;top:856px;width:484px;height:46px;border-radius:50% 50% 0 0/100% 100% 0 0;background:linear-gradient(#e9e3d3,#8d7747)}

.medal{position:absolute;top:948px;width:156px;height:156px;border-radius:50%;border:6px solid var(--gold);box-shadow:0 0 0 10px rgba(0,0,0,.25)}
.medal-fill{position:absolute;inset:4px;border-radius:50%}
.medal-label{position:absolute;left:50%;bottom:10px;transform:translateX(-50%);width:140px;height:18px;background:linear-gradient(var(--gold-light),var(--gold));color:#1a140c;text-align:center;font-family:"Montserrat",sans-serif;font-weight:400;font-size:12px;line-height:18px;white-space:nowrap}
.medal-label b{font-weight:700}

.newsletter{position:absolute;left:376px;top:1134px;display:flex;gap:7px;align-items:center}
.newsletter-text{text-align:right}
.newsletter-title{font-family:"Montserrat",sans-serif;font-weight:400;font-size:12.5px;line-height:15px;letter-spacing:.5px}
.newsletter-title b{font-weight:700}
.newsletter-sub{font-family:"Roboto Condensed",sans-serif;font-size:7.5px;line-height:10px;color:var(--gold)}
.newsletter-input{width:180px;height:28px;border:1.5px solid var(--gold);border-radius:5px;display:flex;align-items:center;justify-content:space-between;padding:0 6px 0 9px;font-size:10px;color:var(--muted)}
.newsletter-go{width:16px;height:16px;border-radius:50%;border:1.5px solid var(--text)}
.footer{position:absolute;left:250px;top:1178px;font-size:7px;color:var(--gold-deep)}
</style>
</head>
<body>
<div class="backdrop" role="img" aria-label="Dim sepia photograph of party guests on a yacht at dusk"></div>
<div class="hero-photo" role="img" aria-label="Cloudy sunset sky over the sea with a woman in a sun hat holding a cocktail"></div>

<header>
  <div class="logo">
    <div class="logo-mark"></div>
    <div>
      <div class="logo-name">MERIDEL</div>
      <div class="logo-sub">SUPER YACHT PARTY IBIZA</div>
    </div>
  </div>
  <nav class="nav">
    <span>HOME</span><span>THE YACHT</span><span>VIP</span><span>TICKETS</span><span>CONTACT</span><span>FAQ</span><span>RECRUITMENT</span>
    <svg class="nav-search" viewBox="0 0 18 18" aria-label="Search"><rect width="18" height="18" rx="4" fill="#f3ede0"/><circle cx="8" cy="8" r="4" fill="none" stroke="#1e170f" stroke-width="2"/><line x1="11" y1="11" x2="14" y2="14" stroke="#1e170f" stroke-width="2" stroke-linecap="round"/></svg>
  </nav>
  <div class="reserve-title"><b>FOR RESERVATIONS</b> &amp; BOOKINGS</div>
  <div class="reserve-line">please contact <span>reservations@meridel-yacht.com</span> or telephone <span>0029 555 010 247</span></div>
  <div class="social">
    <span class="social-label"><b>SOCIAL</b> NETWORK</span>
    <span class="social-dot"></span><span class="social-dot"></span><span class="social-dot"></span><span class="social-dot"></span><span class="social-dot"></span>
  </div>
</header>

<div class="welcome">
  <span class="welcome-small">WELCOME TO</span>
  <span class="welcome-big">MERIDEL</span>
</div>

<main>
  <div class="panel"></div>
  <div class="intro">
    <p>Created by titans of the Ibiza boat and club scene with over 10 years experience the Meridel Super Yacht Parties will define a dawn of a new age for Ibiza Boat Parties where they are no longer confined to the top deck of a sight seeing catamaran.</p>
    <p>Sailing exclusively from San Antonio in 2015, which is the only place to be seen capturing the islands iconic sunset. The San Antonio sunset has served as a backdrop for every major music revolution on the island and the Meridel Super Yacht Experience pulls no punches.</p>
  </div>

  <div class="photo-circle" style="left:272px;background:radial-gradient(circle,#d9cfbd,#8c7b62)" role="img" aria-label="Guest relaxing in a yacht's leather lounge"></div>
  <div class="photo-circle" style="left:406px;background:radial-gradient(circle,#e6e0d4,#8f8576)" role="img" aria-label="Aerial view of a white super yacht deck"></div>
  <div class="claim">NOT ALL<br>BOAT<br>PARTIES<br>ARE<br>CREATED<br>EQUAL</div>
  <div class="photo-circle" style="left:660px;background:radial-gradient(circle,#9c7f55,#3d2e1e)" role="img" aria-label="Guests raising champagne glasses"></div>
  <div class="photo-circle" style="left:792px;background:radial-gradient(circle,#f3dfa8,#8c6a3a)" role="img" aria-label="Crowd dancing at sunset"></div>

  <div class="features">
    <ul class="left">
      <li>Super Yacht Experience</li><li>Iconic Ibiza Sunset</li><li>4 Floors Of Music</li><li>Deep And Tech House</li><li>KRAL Soundsystem</li><li>Vip Rooms And Beds Available</li><li>On Board Local Fashion &amp; Merch Shop</li>
    </ul>
    <ul class="dots"><li>•</li><li>•</li><li>•</li><li>•</li><li>•</li><li>•</li><li>•</li></ul>
    <ul class="right">
      <li>Bottle Service To Tables</li><li>Champagne Spray</li><li>€100 Vodka Bottle</li><li>Wildest Party</li><li>Hottest Girls And Guys</li><li>On Board Hot Tub</li><li>Islands Best Ariel Production At Sea</li>
    </ul>
  </div>

  <div class="events-title">VIEW <b>UPCOMING EVENTS</b></div>
  <div class="events-yacht" role="img" aria-label="Bow of a white super yacht"></div>

  <div class="medal" style="left:331px"><div class="medal-fill" style="background:radial-gradient(circle,#cfc6b6,#5e5446)" role="img" aria-label="Woman in bikini on the beach at sunset"></div><div class="medal-label"><b>IBIZA</b> SUNSET</div></div>
  <div class="medal" style="left:522px"><div class="medal-fill" style="background:radial-gradient(circle,#ece7dd,#8a8274)" role="img" aria-label="Guest lounging on a VIP deck bed"></div><div class="medal-label"><b>VIP</b> SERVICES</div></div>
  <div class="medal" style="left:712px"><div class="medal-fill" style="background:radial-gradient(circle,#f2efe8,#2d5a7a)" role="img" aria-label="Super yacht cruising through blue water"></div><div class="medal-label"><b>SUPER</b> YACHT</div></div>
</main>

<section class="newsletter">
  <div class="newsletter-text">
    <div class="newsletter-title"><b>SUBSCRIBE</b> TO OUR NEWSLETTER</div>
    <div class="newsletter-sub">Sign up for exclusive updates, special offers and more!</div>
  </div>
  <div class="newsletter-input">Email Address<span class="newsletter-go"></span></div>
</section>

<footer class="footer">Copyright © 2015 Super Yacht Party - Meridel. All Rights Reserved.</footer>
</body>
</html>
```